Personal development products that change your life

This is a direct selling business that sells personal development courses, but also sells the business as well if desired. This is not MLM, and there is no handling of the product required, nor hassling friends or family. We are looking for business minded people wanting to work their own hours and achieve a desirable income from this. A success image or happy image on a flyer would be great. I'd like the website address to be displayed as well thanks. www.grow-and-gain.com.au

Target Market(s)

Business-minded individuals searching for more finances. Self motivated, driven, interested in self development.

Industry/Entity Type

Business

Font styles to use
Sans Serif

Requirements
Must have
• Are you looking for
• - a franchise or business?
• - a change of career?
• - a back up income?
• Not MLM
• No product handling or shipping
• No hard sales required
• website: www.grow-and-gain.com.au
Nice to have
• A picture or background of excited person jumping in the air, or some similar.
• Worded to enrol people interested in achieving more financial headway, or flexible hours, or travel and do this business from anywhere in the world.
• Only need access to a phone, internet connection and a desire to succeed.

```html
<!DOCTYPE html>
<html lang="en">
<head>
<meta charset="utf-8">
<title>Grow And Gain – Flyer</title>
<link rel="stylesheet" href="https://fonts.googleapis.com/css2?family=Exo+2:wght@800&family=Questrial&family=Open+Sans:wght@600;700&family=Oswald:wght@500&display=swap">
<style>
  :root {
    --orange: #e2671f;
    --orange-dark: #c9541a;
    --white: #ffffff;
    --ink: #1b1b1b;
    --teal: #2f5f6a;
    --teal-dark: #25505a;
    --grey-light: #d9d9d9;
    --grey-mid: #8f8f8f;
    --grey-dark: #4a4a4a;
    --stage: #3a3f44;
  }
  * { margin: 0; padding: 0; box-sizing: border-box; }
  html, body { width: 900px; height: 1200px; overflow: hidden; background: var(--stage); }
  .flyer {
    position: absolute; left: 48px; top: 32px; width: 804px; height: 1136px;
    overflow: hidden; background: var(--teal);
  }
  .abs { position: absolute; }

  .header {
    left: 0; top: 0; width: 804px; height: 178px;
    background: linear-gradient(90deg, #5a5a5a 0%, #bdbdbd 50%, #5a5a5a 100%);
  }
  .brand-name {
    left: 0; width: 804px; top: 38px; text-align: center;
    font-family: "Exo 2", sans-serif; font-weight: 800; font-size: 78px;
    line-height: 1; color: var(--orange); letter-spacing: 1px;
  }
  .brand-tagline {
    left: 0; width: 804px; top: 121px; text-align: center;
    font-family: "Open Sans", sans-serif; font-weight: 700; font-size: 16.5px; color: var(--white);
  }

  .road-photo {
    left: 0; top: 178px; width: 804px; height: 958px;
    background: linear-gradient(180deg,
      #1f6fc0 0%, #5a9fd8 16%, #b9d4e6 26%, #c9b38f 32%, #a5957d 36%,
      #6e6a66 40%, #3c3a3a 55%, #2e2c2b 75%, #3a3836 100%);
  }
  .road-lines {
    left: 350px; top: 470px; width: 190px; height: 560px;
    background: linear-gradient(90deg, transparent 20%, #e6b022 20%, #e6b022 42%, transparent 42%, transparent 58%, #e6b022 58%, #e6b022 80%, transparent 80%);
    clip-path: polygon(48% 0, 52% 0, 100% 100%, 0 100%);
    opacity: .9;
  }

  .question-banner {
    left: 0; top: 311px; width: 486px; height: 61px;
    background: var(--orange);
    clip-path: polygon(0 0, 100% 0, 94% 100%, 0 100%);
  }
  .question-banner span {
    position: absolute; left: 64px; top: 11px;
    font-family: "Open Sans", sans-serif; font-weight: 600; font-size: 33px; color: var(--white);
  }

  .checklist-panel {
    left: 0; top: 372px; width: 804px; height: 156px;
    background: linear-gradient(90deg, rgba(255,255,255,.85), rgba(255,255,255,.35));
  }
  .checklist { list-style: none; position: absolute; left: 46px; top: 14px; }
  .checklist li {
    display: flex; align-items: center; gap: 10px; height: 47px;
    font-family: "Questrial", sans-serif; font-size: 29px; color: var(--ink);
  }
  .checklist svg { width: 36px; height: 36px; }

  .requirements-band {
    left: 0; top: 528px; width: 804px; height: 80px;
    background: rgba(200,200,200,.78);
  }
  .requirements-band svg { position: absolute; left: 44px; top: 18px; width: 40px; height: 40px; }
  .requirements-band p {
    position: absolute; left: 104px; top: 13px; width: 660px;
    font-family: "Open Sans", sans-serif; font-weight: 700; font-size: 18.5px; line-height: 25px; color: var(--ink);
  }

  .feature-tag {
    left: 0; height: 45px; background: var(--orange);
    clip-path: polygon(0 0, 100% 0, 97% 100%, 0 100%);
    font-family: "Open Sans", sans-serif; font-weight: 600; font-size: 22.5px; color: var(--white);
    padding-left: 73px; line-height: 45px;
  }
  .feature-tag::before {
    content: ""; position: absolute; left: 40px; top: 0; width: 14px; height: 45px;
    background: var(--orange-dark);
    clip-path: polygon(0 0, 100% 50%, 0 100%);
  }
  .tag-mlm { top: 706px; width: 243px; }
  .tag-sales { top: 774px; width: 373px; }
  .tag-shipping { top: 842px; width: 483px; }

  .bottom-curve { left: 0; top: 860px; width: 804px; height: 276px; }

  .balance-badge {
    left: 512px; top: 682px; width: 290px; height: 290px; border-radius: 50%;
    background: rgba(190,190,190,.75);
  }
  .balance-badge div {
    position: absolute; left: 13px; top: 13px; width: 264px; height: 264px; border-radius: 50%;
    background: var(--orange); display: flex; align-items: center; justify-content: center; text-align: center;
    font-family: "Open Sans", sans-serif; font-weight: 600; font-size: 29px; line-height: 39px; color: var(--white);
  }

  .website-pill {
    left: 235px; top: 976px; width: 334px; height: 67px; border-radius: 10px;
    background: linear-gradient(180deg, #6a6a6a, #3d3d3d);
    box-shadow: 0 4px 8px rgba(0,0,0,.45);
    font-family: "Oswald", sans-serif; font-weight: 500; font-size: 24px; color: var(--white);
    text-align: center; line-height: 67px;
  }
  .closing-line {
    left: 0; width: 804px; top: 1060px; text-align: center;
    font-family: "Exo 2", sans-serif; font-weight: 800; font-size: 36px; color: var(--white);
  }
  .closing-line em { font-style: normal; color: var(--orange); }
</style>
</head>
<body>
<main class="flyer">
  <header class="abs header">
    <h1 class="abs brand-name">Grow And Gain</h1>
    <p class="abs brand-tagline">Ongoing personal development opportunities for successful applicants</p>
  </header>

  <div class="abs road-photo" role="img" aria-label="Photo of an open desert highway with double yellow centre lines running to the horizon under a blue sky"></div>

  <div class="abs question-banner"><span>Are you looking for :</span></div>

  <section class="abs checklist-panel">
    <ul class="checklist">
      <li><svg viewBox="0 0 36 36"><circle cx="18" cy="18" r="15" fill="none" stroke="#1b1b1b" stroke-width="3"/><path d="M11 18l5 5 9-11" fill="none" stroke="#1b1b1b" stroke-width="4" stroke-linecap="round" stroke-linejoin="round"/></svg>a franchise or business?</li>
      <li><svg viewBox="0 0 36 36"><circle cx="18" cy="18" r="15" fill="none" stroke="#1b1b1b" stroke-width="3"/><path d="M11 18l5 5 9-11" fill="none" stroke="#1b1b1b" stroke-width="4" stroke-linecap="round" stroke-linejoin="round"/></svg>a change of career?</li>
      <li><svg viewBox="0 0 36 36"><circle cx="18" cy="18" r="15" fill="none" stroke="#1b1b1b" stroke-width="3"/><path d="M11 18l5 5 9-11" fill="none" stroke="#1b1b1b" stroke-width="4" stroke-linecap="round" stroke-linejoin="round"/></svg>a back up income?</li>
    </ul>
  </section>

  <section class="abs requirements-band">
    <svg viewBox="0 0 40 40"><circle cx="20" cy="20" r="17" fill="none" stroke="#1b1b1b" stroke-width="3"/><rect x="13" y="11" width="8" height="15" fill="#1b1b1b"/><rect x="17" y="16" width="10" height="14" fill="#1b1b1b"/></svg>
    <p>All you need is a laptop, a phone,&nbsp; internet connection, a strong desire to succeed,&nbsp; and dedicate 15-20 hours per week</p>
  </section>

  <svg class="abs bottom-curve" viewBox="0 0 804 276" preserveAspectRatio="none">
    <path d="M0 0 Q402 210 804 0 L804 276 L0 276 Z" fill="var(--teal)"/>
  </svg>

  <div class="abs feature-tag tag-mlm">Not MLM</div>
  <div class="abs feature-tag tag-sales">No hard sales required</div>
  <div class="abs feature-tag tag-shipping">No product handling or shipping</div>

  <div class="abs balance-badge"><div>Start the work /<br>life balance<br>you've always<br>wanted</div></div>

  <div class="abs website-pill">WWW.GROW-AND-GAIN.COM.AU</div>
  <p class="abs closing-line">Turn this into <em>DOING</em> what <em>YOU</em> love!</p>
</main>
</body>
</html>
```